Bref créative
ZARVEN Skin Care
Bright & Fun-filled
Maribel Dunstan
Owner
none on card
zarvenbodycare@plumtree-mail.com
www.zarvenbodycare-shop.com
Natural Skin Care Solutions

```html
<!DOCTYPE html>
<html lang="en">
<head>
<meta charset="utf-8">
<title>ZARVEN Skin Care – Business Cards</title>
<link href="https://fonts.googleapis.com/css2?family=Didact+Gothic&family=Questrial&display=swap" rel="stylesheet">
<style>
  :root{
    --backdrop:#ebe7e1;
    --card:#ffffff;
    --ink:#7a7a7a;
    --ink-dark:#5b5b5b;
    --green:#6e9a1e;
    --green-light:#a9c94a;
    --green-dark:#4d7410;
    --gold:#e2b21c;
    --gold-light:#f7dc6a;
    --gold-dark:#b98a0a;
    --band:#f6ef9a;
    --swoosh:#b9b9b9;
  }
  *{box-sizing:border-box;margin:0;padding:0}
  html,body{width:1200px;height:1033px;overflow:hidden}
  body{background:var(--backdrop);position:relative;font-family:"Didact Gothic",sans-serif;color:var(--ink)}
  .card{position:absolute;width:230px;height:400px;border-radius:14px;background:var(--card);overflow:hidden;box-shadow:0 4px 12px rgba(0,0,0,.18)}
  .front .brand{position:absolute;top:30px;left:0;right:0;text-align:center;font-family:"Questrial",sans-serif;font-size:34px;letter-spacing:2px;color:var(--ink)}
  .front .brand .dot{display:inline-block;width:9px;height:9px;border-radius:50%;background:var(--green);margin-left:5px;vertical-align:super}
  .front .rule{position:absolute;top:82px;left:44px;right:44px;height:2px;background:linear-gradient(90deg,transparent,var(--green-light),transparent)}
  .front .name{position:absolute;top:148px;left:0;right:0;text-align:center;font-size:14px;letter-spacing:.5px;color:var(--green-dark)}
  .front .role{position:absolute;top:168px;left:0;right:0;text-align:center;font-size:8px;letter-spacing:1px;color:var(--ink)}
  .front .tagline{position:absolute;top:200px;left:22px;right:22px;height:26px;line-height:26px;text-align:center;font-family:"Questrial",sans-serif;font-style:italic;font-size:15px;color:var(--green);background:linear-gradient(90deg,rgba(246,239,154,0),var(--band) 30%,var(--band) 70%,rgba(246,239,154,0))}
  .front .contact{position:absolute;top:250px;left:22px;list-style:none;font-size:6.5px;line-height:11px;color:var(--ink-dark)}
  .front .wave{position:absolute;left:0;bottom:0;width:230px;height:130px}
  .back .brand{position:absolute;top:50%;left:50%;transform:translate(-50%,-50%) rotate(90deg);font-family:"Questrial",sans-serif;font-size:46px;letter-spacing:3px;color:var(--ink);white-space:nowrap}
  .back .brand .dot{display:inline-block;width:11px;height:11px;border-radius:50%;background:var(--green);margin-left:6px;vertical-align:middle}
  .back .web{position:absolute;bottom:16px;left:0;right:0;text-align:center;font-size:6.5px;color:var(--ink-dark)}
  .framed .inner{position:absolute;inset:10px 10px 36px;border-radius:10px;background:var(--card)}
  .back-gold-frame{background:linear-gradient(135deg,var(--gold-light),var(--gold) 50%,var(--gold-dark))}
  .back-green-frame{background:linear-gradient(160deg,var(--green-light),var(--green) 60%,var(--green-dark))}
  .back-gold-solid{background:linear-gradient(135deg,var(--gold-light),var(--gold) 55%,var(--gold-dark))}
  .back-gold-solid .brand{color:#fff6d0}
  .back-gold-solid .brand .dot{background:#fff6d0}
  .back-gold-solid .web{color:#7a5a00}
  .framed .web{color:#fff}
</style>
</head>
<body>

<!-- Top row -->
<div class="card front" style="left:103px;top:103px">
  <div class="brand">ZARVEN<span class="dot"></span></div>
  <div class="rule"></div>
  <div class="name">MARIBEL DUNSTAN</div>
  <div class="role">OWNER</div>
  <div class="tagline">Naturally Luxurious</div>
  <ul class="contact">
    <li>zarvenbodycare@plumtree-mail.com</li>
    <li>www.zarvenbodycare-shop.com</li>
    <li>Natural Skin Care Solutions</li>
  </ul>
  <svg class="wave" viewBox="0 0 230 130" aria-hidden="true">
    <defs><linearGradient id="g1" x1="0" y1="0" x2="0" y2="1"><stop offset="0" stop-color="var(--green-light)"/><stop offset="1" stop-color="var(--green-dark)"/></linearGradient></defs>
    <path d="M0 40 C70 10 150 70 230 30 L230 48 C150 88 70 30 0 60 Z" fill="var(--swoosh)"/>
    <path d="M0 62 C70 32 150 92 230 50 L230 130 L0 130 Z" fill="url(#g1)"/>
    <rect x="150" y="58" width="60" height="44" rx="14" fill="#c7df7a" role="img" aria-label="Green leaf illustration"/>
  </svg>
</div>

<div class="card front" style="left:349px;top:103px">
  <div class="brand">ZARVEN<span class="dot"></span></div>
  <div class="rule"></div>
  <div class="name">MARIBEL DUNSTAN</div>
  <div class="role">OWNER</div>
  <div class="tagline">Naturally Luxurious</div>
  <ul class="contact">
    <li>zarvenbodycare@plumtree-mail.com</li>
    <li>www.zarvenbodycare-shop.com</li>
    <li>Natural Skin Care Solutions</li>
  </ul>
  <svg class="wave" viewBox="0 0 230 130" aria-hidden="true">
    <defs><linearGradient id="g2" x1="0" y1="0" x2="0" y2="1"><stop offset="0" stop-color="var(--gold-light)"/><stop offset="1" stop-color="var(--gold-dark)"/></linearGradient></defs>
    <path d="M0 40 C70 10 150 70 230 30 L230 48 C150 88 70 30 0 60 Z" fill="var(--swoosh)"/>
    <path d="M0 62 C70 32 150 92 230 50 L230 130 L0 130 Z" fill="url(#g2)"/>
    <rect x="150" y="58" width="60" height="44" rx="14" fill="#b5cf5a" role="img" aria-label="Green leaf illustration"/>
  </svg>
</div>

<div class="card back framed back-gold-frame" style="left:608px;top:103px">
  <div class="inner"></div>
  <div class="brand">ZARVEN<span class="dot"></span></div>
  <div class="web" style="color:#5b4300">www.zarvenbodycare-shop.com</div>
</div>

<div class="card back back-gold-solid" style="left:860px;top:103px">
  <div class="brand">ZARVEN<span class="dot"></span></div>
  <div class="web">www.zarvenbodycare-shop.com</div>
</div>

<!-- Bottom row -->
<div class="card front" style="left:215px;top:516px">
  <div class="brand">ZARVEN<span class="dot"></span></div>
  <div class="rule"></div>
  <div class="name">MARIBEL DUNSTAN</div>
  <div class="role">OWNER</div>
  <div class="tagline">Naturally Luxurious</div>
  <ul class="contact">
    <li>zarvenbodycare@plumtree-mail.com</li>
    <li>www.zarvenbodycare-shop.com</li>
    <li>Natural Skin Care Solutions</li>
  </ul>
  <svg class="wave" viewBox="0 0 230 130" aria-hidden="true">
    <defs><linearGradient id="g3" x1="0" y1="0" x2="0" y2="1"><stop offset="0" stop-color="var(--green-light)"/><stop offset="1" stop-color="var(--green-dark)"/></linearGradient></defs>
    <path d="M0 40 C70 10 150 70 230 30 L230 48 C150 88 70 30 0 60 Z" fill="var(--swoosh)"/>
    <path d="M0 62 C70 32 150 92 230 50 L230 130 L0 130 Z" fill="url(#g3)"/>
    <rect x="150" y="58" width="60" height="44" rx="14" fill="#c7df7a" role="img" aria-label="Green leaf illustration"/>
  </svg>
</div>

<div class="card back framed back-green-frame" style="left:469px;top:516px">
  <div class="inner"></div>
  <div class="brand">ZARVEN<span class="dot"></span></div>
  <div class="web">www.zarvenbodycare-shop.com</div>
</div>

<div class="card back" style="left:731px;top:516px">
  <div class="brand">ZARVEN<span class="dot"></span></div>
  <div class="web">www.zarvenbodycare-shop.com</div>
</div>

</body>
</html>
```